418 5 minute epoxy adhesive

Hi, i need a label for the front and pack of our New Product.
Just our Vellarn Resins Logo on the front and product name. ( as above)
and Vellarn Fibreglass Logo on the back with mixing instructions on the back.

```html
<!DOCTYPE html>
<html lang="en">
<head>
<meta charset="utf-8">
<title>Vellarn 418 Series – Front and Back Labels</title>
<link rel="stylesheet" href="https://fonts.googleapis.com/css2?family=Oswald:wght@700&family=Saira:ital,wght@0,300;0,400;0,600;0,700;0,800;1,700;1,800&display=swap">
<style>
  :root{
    --stage:#3d3d3d;
    --paper:#ffffff;
    --blue:#1a56b0;
    --blue-deep:#0e3f94;
    --frame-blue:#1552a8;
    --violet:#3f3f99;
    --red:#e8262d;
    --caption:#d6d6d6;
    --mist:#e6e6e8;
  }
  *{box-sizing:border-box;margin:0;padding:0}
  html,body{width:1006px;height:1200px;overflow:hidden}
  body{background:var(--stage);position:relative;font-family:"Saira",sans-serif}
  .label{position:absolute;display:block}
  .label--front{left:38px;top:390px;width:468px;height:374px}
  .label--back{left:590px;top:388px;width:378px;height:377px}
  .size-caption{position:absolute;top:798px;font-family:"Saira",sans-serif;font-weight:300;font-size:15px;letter-spacing:.06em;color:var(--caption)}
  .size-caption--front{left:44px}
  .size-caption--back{left:582px}
  .t-display{font-family:"Saira",sans-serif;font-style:italic;font-weight:800}
  .t-heading{font-family:"Saira",sans-serif;font-style:italic;font-weight:700}
  .t-series{font-family:"Oswald",sans-serif;font-weight:700}
  .t-series-back{font-family:"Saira",sans-serif;font-weight:800}
  .t-brand{font-family:"Saira",sans-serif;font-weight:800}
  .t-body{font-family:"Saira",sans-serif;font-weight:400}
  .t-body-strong{font-weight:700}
  .t-note{font-family:"Saira",sans-serif;font-weight:600}
</style>
</head>
<body>

<svg class="label label--front" viewBox="0 0 468 374" aria-label="Front label: Vellarn Resins 5 minute epoxy adhesive 418 Series">
  <defs>
    <linearGradient id="front-blue" x1="0" y1="0" x2="0" y2="1">
      <stop offset="0" stop-color="var(--blue)"/>
      <stop offset="1" stop-color="var(--blue-deep)"/>
    </linearGradient>
    <linearGradient id="front-mist" x1="0" y1="0" x2="1" y2="1">
      <stop offset="0" stop-color="var(--mist)"/>
      <stop offset=".5" stop-color="#ffffff"/>
      <stop offset="1" stop-color="var(--mist)"/>
    </linearGradient>
    <clipPath id="front-clip"><rect x="7" y="7" width="454" height="360" rx="12"/></clipPath>
  </defs>
  <rect width="468" height="374" fill="var(--paper)"/>
  <g clip-path="url(#front-clip)">
    <rect x="7" y="7" width="454" height="360" fill="url(#front-blue)"/>
    <path class="header-field" d="M7 7H461V102Q234 132 7 106Z" fill="url(#front-mist)" role="img" aria-label="Soft grey wave texture"/>
    <path d="M7 330Q234 304 461 330" fill="none" stroke="var(--paper)" stroke-width="2.5"/>
    <path class="footer-band" d="M7 335Q234 309 461 335V367H7Z" fill="var(--red)"/>
  </g>
  <rect x="7" y="7" width="454" height="360" rx="12" fill="none" stroke="var(--frame-blue)" stroke-width="3"/>

  <g class="brand">
    <circle cx="78" cy="58" r="20" fill="var(--red)"/>
    <text class="t-brand" x="110" y="70" font-size="34" fill="var(--blue)" textLength="290" lengthAdjust="spacingAndGlyphs">VELLARN RESINS</text>
    <text class="t-brand" x="252" y="100" font-size="11.5" fill="var(--blue)" text-anchor="middle" letter-spacing="1.5">BUILT TO BOND HARD</text>
  </g>

  <rect x="124" y="131" width="213" height="40" rx="14" fill="var(--red)"/>
  <text class="t-display" x="230" y="163" font-size="34" fill="var(--paper)" text-anchor="middle" textLength="168" lengthAdjust="spacingAndGlyphs">5 MINUTE</text>
  <text class="t-heading" x="230" y="218" font-size="44" fill="var(--paper)" text-anchor="middle" textLength="380" lengthAdjust="spacingAndGlyphs">EPOXY ADHESIVE</text>
  <text class="t-series" x="232" y="305" font-size="92" fill="var(--paper)" text-anchor="middle" textLength="358" lengthAdjust="spacingAndGlyphs">418 SERIES</text>
  <text class="t-display" x="233" y="358" font-size="27" fill="var(--paper)" text-anchor="middle" textLength="165" lengthAdjust="spacingAndGlyphs">200 MLS KIT</text>
  <text class="t-note" x="354" y="358" font-size="6.5" fill="var(--paper)" textLength="88" lengthAdjust="spacingAndGlyphs">Read Caustions on the back panel</text>
</svg>

<svg class="label label--back" viewBox="0 0 378 377" aria-label="Back label: Vellarn Fibreglass 418 Series mixing instructions">
  <defs>
    <linearGradient id="back-mist" x1="0" y1="0" x2="1" y2="1">
      <stop offset="0" stop-color="var(--mist)"/>
      <stop offset=".5" stop-color="#ffffff"/>
      <stop offset="1" stop-color="var(--mist)"/>
    </linearGradient>
    <clipPath id="back-clip"><rect x="10" y="10" width="358" height="357" rx="10"/></clipPath>
  </defs>
  <rect width="378" height="377" fill="var(--paper)"/>
  <g clip-path="url(#back-clip)">
    <rect x="10" y="10" width="358" height="357" fill="var(--violet)"/>
    <path class="header-field" d="M10 10H368V100Q189 124 10 100Z" fill="url(#back-mist)" role="img" aria-label="Soft grey wave texture"/>
    <path d="M10 331Q189 319 368 331" fill="none" stroke="var(--paper)" stroke-width="2"/>
    <path class="footer-band" d="M10 335Q189 323 368 335V367H10Z" fill="var(--red)"/>
  </g>
  <rect x="10" y="10" width="358" height="357" rx="10" fill="none" stroke="var(--frame-blue)" stroke-width="3"/>

  <g class="brand">
    <text class="t-brand" x="189" y="70" font-size="30" fill="var(--red)" text-anchor="middle" textLength="140" lengthAdjust="spacingAndGlyphs">VELLARN</text>
    <text class="t-brand" x="189" y="90" font-size="13" fill="var(--red)" text-anchor="middle" textLength="160" lengthAdjust="spacingAndGlyphs">FIBREGLASS</text>
  </g>

  <text class="t-display" x="189" y="152" font-size="22" fill="var(--red)" text-anchor="middle" textLength="306" lengthAdjust="spacingAndGlyphs">5 MINUTE EPOXY ADHESIVE</text>
  <text class="t-series-back" x="189" y="189" font-size="34" fill="var(--paper)" text-anchor="middle" textLength="198" lengthAdjust="spacingAndGlyphs">418 SERIES</text>

  <g class="t-body" font-size="10" fill="var(--paper)">
    <text x="32" y="214" textLength="315" lengthAdjust="spacingAndGlyphs"><tspan class="t-body-strong">418 Series</tspan> is a two part, free flowing, liquid epoxy adhesive with a</text>
    <text x="32" y="227.5" textLength="315" lengthAdjust="spacingAndGlyphs">rapid 5 minute cure time. It can be used on a wide range of materials</text>
    <text x="32" y="241" textLength="315" lengthAdjust="spacingAndGlyphs">showing excellent adhesion and superior strength. 418 Series is the</text>
    <text x="32" y="254.5" textLength="315" lengthAdjust="spacingAndGlyphs">perfect adhesive to have for all those general purpose projects. It is</text>
    <text x="32" y="268" textLength="315" lengthAdjust="spacingAndGlyphs">formulated to be mixed at a easy 1:1 ratio and can even have fillers</text>
    <text x="32" y="281.5" textLength="315" lengthAdjust="spacingAndGlyphs">added to create a thickened glue paste. With an almost endless shelf</text>
    <text x="32" y="295" textLength="315" lengthAdjust="spacingAndGlyphs">life 418 Series is the one glue that is needed in every shed in Australia.</text>
    <text x="32" y="308.5" textLength="315" lengthAdjust="spacingAndGlyphs">Skip the old Grivex and buy some of Vellarn's 418 Series, its a massive</text>
    <text x="189" y="322" text-anchor="middle">630% cheaper and far superior.</text>
  </g>

  <text class="t-note" x="189" y="356" font-size="12" fill="var(--paper)" text-anchor="middle" textLength="244" lengthAdjust="spacingAndGlyphs">Mix at a ratio of 1 Part A : 1 Part B (418A : 418B)</text>
</svg>

<p class="size-caption size-caption--front">100MM X 80MM</p>
<p class="size-caption size-caption--back">100MM X 100MM</p>

</body>
</html>
```